RUVO WARE LTD

Advertisement to get more schools:
use website https://www.ruvo-ware.co.uk for logos etc.
ICT Service Level Agreements for as little as £2000 per year
Unlimited Remote, phone and email support
Unlimited Call outs included
90% fix time within 30 minutes of ticket submission
Extra support during Scolvar inspections
GDPR service included

Education

```html
<!DOCTYPE html>
<html lang="en">
<head>
<meta charset="utf-8">
<title>Ruvo Ware – ICT Support for Schools</title>
<link href="https://fonts.googleapis.com/css2?family=Montserrat:wght@600;700&family=Lato:wght@400;700&display=swap" rel="stylesheet">
<style>
  :root{
    --blue:#0b6fb8;
    --orange:#f47f45;
    --dark:#222222;
    --white:#ffffff;
    --hero-a:#c9ccd2;
    --hero-b:#6f4a44;
  }
  *{box-sizing:border-box;margin:0;padding:0}
  html,body{width:1200px;height:3496px;overflow:hidden;background:var(--white)}
  .canvas{position:relative;width:1200px;height:3496px;font-family:"Montserrat",sans-serif}
  .top-bar{position:absolute;left:0;top:0;width:1200px;height:6px;background:linear-gradient(90deg,var(--blue) 0 49%,var(--orange) 49% 100%)}
  .brand{position:absolute;left:0;width:1200px;text-align:center;font-family:"Montserrat",sans-serif;font-weight:700;font-size:56px;letter-spacing:3px;line-height:1}
  .brand--header{top:42px;color:var(--blue)}
  .brand--footer{top:2950px;color:var(--orange)}

  .hero{position:absolute;left:0;top:145px;width:1200px;height:600px}
  .hero__photo{position:absolute;inset:0;background:linear-gradient(100deg,var(--hero-a) 0%,#9aa0a8 30%,var(--hero-b) 50%,#8d8f93 75%,#b8bcc0 100%)}
  .hero__frame{position:absolute;left:564px;top:50px;width:576px;height:502px;border:4px solid var(--orange);border-radius:70px 0 70px 0}
  .hero__panel{position:absolute;left:578px;top:62px;width:547px;height:478px;background:rgba(11,111,184,.9);border-radius:64px 0 64px 0;color:var(--white);text-align:center;padding-top:100px}
  .hero__title{font-weight:700;font-size:30px;line-height:52px;letter-spacing:.5px}
  .hero__text{font-family:"Lato",sans-serif;font-size:22px;line-height:52px;margin-top:2px}

  .feature-icon{position:absolute;width:300px;height:263px;border:4.5px solid;border-radius:50px 0 50px 0}
  .feature-icon__fill{position:absolute;left:9px;top:8px;right:9px;bottom:8px;border-radius:44px 0 44px 0;display:flex;align-items:center;justify-content:center}
  .feature-icon--blue{border-color:var(--orange)}
  .feature-icon--blue .feature-icon__fill{background:var(--blue)}
  .feature-icon--orange{border-color:var(--blue)}
  .feature-icon--orange .feature-icon__fill{background:var(--orange)}
  .feature-icon svg{width:200px;height:170px}

  .feature-text{position:absolute;font-weight:700;font-size:39px;line-height:52.5px;color:var(--blue);letter-spacing:.5px}
  .feature-text--left{left:633px;text-align:left}
  .feature-text--right{text-align:right}
  .accent{color:var(--orange)}

  .footer{position:absolute;left:0;top:2838px;width:1200px;height:658px;background:var(--dark)}
  .footer__info{position:absolute;left:0;top:3088px;width:1200px;text-align:center;color:var(--white);font-family:"Lato",sans-serif;font-size:25px;line-height:52.5px}
  .social{position:absolute;top:3267px;left:481px;display:flex;gap:27px}
  .social__item{width:60px;height:60px;border:1.5px dashed #8a8a8a;border-radius:4px;display:flex;align-items:center;justify-content:center}
  .social__item span{width:30px;height:30px;background:var(--white);border-radius:4px}
  .copyright{position:absolute;left:0;top:3373px;width:1200px;text-align:center;color:var(--white);font-family:"Lato",sans-serif;font-size:22px}
</style>
</head>
<body>
<div class="canvas">
  <div class="top-bar"></div>
  <div class="brand brand--header">RUVO WARE</div>

  <section class="hero">
    <div class="hero__photo" role="img" aria-label="Photo of a pupil wearing a virtual reality headset in a classroom"></div>
    <div class="hero__frame"></div>
    <div class="hero__panel">
      <h1 class="hero__title">EDUCATION, SUPPORT AND<br>INSTALLATION OF ALL<br>TECHNOLOGIES</h1>
      <p class="hero__text">We offer fast, flexible, reliable and<br>cost-effective ICT support for Education</p>
    </div>
  </section>

  <!-- SLA -->
  <div class="feature-icon feature-icon--blue" style="left:309px;top:922px">
    <div class="feature-icon__fill">
      <svg viewBox="0 0 200 170" fill="none" stroke="#fff" stroke-width="6" stroke-linecap="round" stroke-linejoin="round">
        <path d="M22 50 L40 30 L70 52 L55 90 Z"/>
        <path d="M178 50 L160 30 L130 52 L145 90 Z"/>
        <path d="M68 56 L98 44 L124 48 L100 72 L86 66"/>
        <path d="M132 60 L142 88 L112 120 L96 132"/>
        <circle cx="70" cy="104" r="9"/><circle cx="82" cy="116" r="9"/><circle cx="94" cy="128" r="9"/><circle cx="106" cy="138" r="9"/>
      </svg>
    </div>
  </div>
  <p class="feature-text feature-text--left" style="top:976px">ICT SLA <span class="accent">AGREEMENTS</span><br>FOR AS LITTLE AS £2000<br>PER YEAR</p>

  <!-- Unlimited support -->
  <div class="feature-icon feature-icon--orange" style="left:579px;top:1207px">
    <div class="feature-icon__fill">
      <svg viewBox="0 0 200 170" fill="none" stroke="#fff" stroke-width="6" stroke-linecap="round">
        <path d="M100 85 C80 50 40 50 38 85 C40 120 80 120 100 85 C120 50 160 50 162 85 C160 120 120 120 100 85 Z"/>
        <path d="M100 85 C84 62 52 62 52 85 C52 108 84 108 100 85 C116 62 148 62 148 85 C148 108 116 108 100 85"/>
      </svg>
    </div>
  </div>
  <p class="feature-text feature-text--right" style="right:698px;top:1261px">UNLIMITED <span class="accent">REMOTE,</span><br><span class="accent">PHONE AND EMAIL</span><br>SUPPORT</p>

  <!-- Call outs -->
  <div class="feature-icon feature-icon--blue" style="left:309px;top:1534px">
    <div class="feature-icon__fill">
      <svg viewBox="0 0 200 170" fill="none" stroke="#fff" stroke-width="6" stroke-linecap="round" stroke-linejoin="round">
        <path d="M62 30 L78 26 L90 56 L78 66 C86 86 98 98 116 106 L126 94 L156 106 L152 122 C146 134 134 140 120 136 C88 126 62 100 52 66 C48 50 52 38 62 30 Z"/>
        <path d="M112 40 C128 44 138 54 142 70"/>
        <path d="M116 22 C142 28 156 44 162 66"/>
      </svg>
    </div>
  </div>
  <p class="feature-text feature-text--left" style="top:1588px">UNLIMITED <span class="accent">CALL</span><br><span class="accent">OUTS</span> INCLUDED</p>

  <!-- Fix time -->
  <div class="feature-icon feature-icon--orange" style="left:579px;top:1819px">
    <div class="feature-icon__fill">
      <svg viewBox="0 0 200 170" fill="none" stroke="#fff" stroke-width="5" stroke-linecap="round" stroke-linejoin="round">
        <path d="M62 120 V18 H122 L140 36 V120"/>
        <path d="M122 18 V36 H140"/>
        <path d="M48 90 V132 H152 V90"/>
        <path d="M36 132 H164 V140 H36 Z"/>
        <path d="M72 44 l5 5 l9 -10 M72 66 l5 5 l9 -10 M72 88 l5 5 l9 -10"/>
        <path d="M94 46 H128 M94 68 H128 M94 90 H128 M94 106 H128"/>
      </svg>
    </div>
  </div>
  <p class="feature-text feature-text--right" style="right:698px;top:1873px">90% FIX TIME WITHIN<br><span class="accent">30 MINUTES</span> OF<br>TICKET SUBMISSION</p>

  <!-- Inspections -->
  <div class="feature-icon feature-icon--blue" style="left:309px;top:2175px">
    <div class="feature-icon__fill">
      <svg viewBox="0 0 200 170" fill="none" stroke="#fff" stroke-width="5" stroke-linecap="round" stroke-linejoin="round">
        <rect x="120" y="14" width="44" height="30" rx="4"/>
        <path d="M130 44 L126 54 L140 44 M130 26 H154 M130 34 H148"/>
        <circle cx="100" cy="78" r="22"/>
        <path d="M72 80 C72 56 86 46 100 46 C114 46 128 56 128 80"/>
        <path d="M62 140 C64 116 80 106 100 106 C120 106 136 116 138 140 Z"/>
        <path d="M40 110 L50 104 L58 118 L52 124 C56 132 62 138 70 142 L58 150 C48 142 40 126 40 110 Z"/>
        <path d="M60 40 C46 52 40 68 42 86 M40 52 L60 40 L62 58"/>
        <path d="M152 70 C160 94 152 118 134 132 M150 86 L152 70 L164 82"/>
      </svg>
    </div>
  </div>
  <p class="feature-text feature-text--left" style="top:2243px">EXTRA <span class="accent">SUPPORT</span> DURING<br>SCOLVAR INSPECTIONS</p>

  <!-- GDPR -->
  <div class="feature-icon feature-icon--orange" style="left:579px;top:2460px">
    <div class="feature-icon__fill">
      <svg viewBox="0 0 200 170" fill="none" stroke="#fff" stroke-width="5" stroke-linecap="round" stroke-linejoin="round">
        <rect x="48" y="14" width="96" height="130" rx="8"/>
        <text x="96" y="48" text-anchor="middle" fill="#fff" stroke="none" font-family="Montserrat,sans-serif" font-weight="700" font-size="28" letter-spacing="3">GDPR</text>
        <rect x="62" y="92" width="34" height="30" rx="3"/>
        <path d="M68 92 V82 C68 70 90 70 90 82 V92"/>
        <path d="M104 70 H132 M110 82 H132"/>
        <path d="M138 100 L158 108 V124 C158 138 148 146 138 152 C128 146 118 138 118 124 V108 Z"/>
        <path d="M129 124 l7 7 l12 -13"/>
      </svg>
    </div>
  </div>
  <p class="feature-text feature-text--right" style="right:710px;top:2543px"><span class="accent">GDPR</span> SERVICE<br>INCLUDED</p>

  <footer class="footer"></footer>
  <div class="brand brand--footer">RUVO WARE</div>
  <div class="footer__info">
    Ruvo Ware, is a registered UK Limited Company<br>
    Company Number: 10482736<br>
    VAT Number: GB318540927
  </div>
  <div class="social" aria-label="Social links">
    <div class="social__item"><span></span></div>
    <div class="social__item"><span></span></div>
    <div class="social__item"><span></span></div>
  </div>
  <p class="copyright">© copyrights 2022 Ruvo Ware &nbsp;|&nbsp;&nbsp; All rights reserved.</p>
</div>
</body>
</html>
```